Flat bootstrap design for existing site

I'm looking for a modern flat design based around an existing logo. This has to be a custom design (no external templates), and implemented into a bootstrap framework.

The logo is attached as 2 versions - choose whichever you want, that flows better with whatever design you choose.

Added screenshots of the existing site (currently using the default bootstrap layouts). Please make your designs around those pages in the screenshots (i.e. the homepage only has the postal code input and the header). The active page has 3 screenshots, because I wanted to illustrate the other states that would be visible (in the table rows).

This is a moving/junk removal website, just for some context.

Here's some example websites (flat designs) that I like, just to give you an idea of what I'm after.

https://www.plimvora.com/
https://dacklow.com/
https://trevanu.com/
https://quobrintal.com/en/

Coding

Coded - Design and coding required

Number of Pages Required

5+ page

Colors

Designer to choose colors to be used in the design.

Requirements
Must have
• It must be a modern/simple flat design, that is built around the existing logo (attached).
• It has to be implemented using bootstrap.

```html
<!DOCTYPE html>
<html lang="en">
<head>
<meta charset="utf-8">
<title>Haulvee — Junk Removal</title>
<link href="https://fonts.googleapis.com/css2?family=Roboto:wght@400;500;700&display=swap" rel="stylesheet">
<style>
  :root {
    --sky: #48c8f5;
    --sky-text: #4cc3f1;
    --white: #ffffff;
    --panel: rgba(40, 36, 34, 0.55);
    --field-text: #555555;
    --hero-warm: #7b5a47;
    --hero-mid: #6b6460;
    --hero-cool: #3e4d63;
  }
  * { margin: 0; padding: 0; box-sizing: border-box; }
  html, body { width: 1200px; height: 677px; overflow: hidden; }
  body { font-family: 'Roboto', sans-serif; position: relative; background: var(--hero-mid); }

  .site-header {
    position: absolute; top: 0; left: 0; width: 1200px; height: 101px;
    background: var(--sky); z-index: 2;
  }
  .brand {
    position: absolute; left: 110px; top: 32px;
    display: flex; align-items: center; gap: 10px;
    color: var(--white); font-weight: 700; font-size: 30px; letter-spacing: 1px;
  }
  .brand-dot { width: 14px; height: 14px; border-radius: 50%; background: var(--white); }
  .main-nav a {
    position: absolute; top: 34px; height: 33px; line-height: 33px;
    color: var(--white); font-size: 13px; font-weight: 500; text-decoration: none;
  }
  .nav-book { left: 665px; }
  .nav-how { left: 744px; }
  .nav-driver {
    left: 881px; width: 133px; text-align: center;
    background: var(--white); color: var(--sky-text) !important; border-radius: 3px;
  }
  .nav-signin { left: 1056px; }

  .hero-photo {
    position: absolute; top: 101px; left: 0; width: 1200px; height: 576px;
    background: linear-gradient(100deg, var(--hero-warm) 0%, var(--hero-mid) 45%, var(--hero-cool) 75%, var(--hero-mid) 100%);
  }

  .booking-panel {
    position: absolute; left: 99px; top: 225px; width: 1003px; height: 248px;
    background: var(--panel); z-index: 1;
  }
  .booking-title {
    position: absolute; top: 56px; width: 100%; text-align: center;
    color: var(--sky-text); font-size: 33px; font-weight: 500;
  }
  .postal-field {
    position: absolute; left: 173px; top: 134px; width: 453px; height: 52px;
    border: none; border-radius: 26px; background: var(--white);
    padding-left: 24px; font-family: 'Roboto', sans-serif; font-size: 12px; color: var(--field-text);
  }
  .postal-field::placeholder { color: var(--field-text); }
  .book-button {
    position: absolute; left: 653px; top: 134px; width: 179px; height: 52px;
    border: none; border-radius: 26px; background: var(--sky);
    color: var(--white); font-family: 'Roboto', sans-serif; font-size: 21px; font-weight: 400;
  }

  .site-footer {
    position: absolute; left: 99px; top: 603px; width: 1003px;
    border-top: 1px solid rgba(255,255,255,0.6); z-index: 1;
  }
  .copyright {
    margin-top: 26px; text-align: center;
    color: var(--white); font-size: 12px;
  }
</style>
</head>
<body>
  <header class="site-header">
    <div class="brand"><span class="brand-dot"></span>HAULVEE</div>
    <nav class="main-nav">
      <a class="nav-book" href="#">BOOK</a>
      <a class="nav-how" href="#">HOW IT WORKS</a>
      <a class="nav-driver" href="#">BECOME A DRIVER</a>
      <a class="nav-signin" href="#">SIGN IN</a>
    </nav>
  </header>

  <div class="hero-photo" role="img" aria-label="Background photo of a smiling man working at a laptop in a warm office"></div>

  <section class="booking-panel">
    <h1 class="booking-title">Need Junk Removed? Book now</h1>
    <input class="postal-field" type="text" placeholder="Postal Code">
    <button class="book-button" type="button">BOOK NOW</button>
  </section>

  <footer class="site-footer">
    <p class="copyright">© 2017 Haulvee . All rights reserved.</p>
  </footer>
</body>
</html>
```